New business card/stationary for a consulting company

I am looking for a clean and very professional looking business card for my consulting company as well as corresponding stationary. I am uploading our logo. I like simple and powerful for the feel. No graphics but I am open on everything else. Below is my contact information but would like the final to be in a version I can add my employees information into and print. Thank you.

Daniel Whitcombe
dan@ferncliffadvisory.com
2870 North 9th Avenue, Summit Floor, Elm Ridge, Illinois 60531
www.ferncliffadvisory.com

Industry/Entity Type

Consulting

Contact Information for Business Card

Daniel Whitcombe
dan@ferncliffadvisory.com
www.ferncliffadvisory.com

Font styles to use
Serif
Sans Serif

Requirements
Must have
• Our logo and the business card details.
Nice to have
• our website www.ferncliffadvisory.com

```html
<!DOCTYPE html>
<html lang="en">
<head>
<meta charset="utf-8">
<title>Ferncliff Advisory – Business Card</title>
<link rel="stylesheet" href="https://fonts.googleapis.com/css2?family=Montserrat:wght@300;700&family=Source+Sans+3:wght@400;700&display=swap">
<style>
  :root {
    --navy: #16137c;
    --navy-deep: #0f0d66;
    --paper: #ffffff;
    --backdrop: #e6e7ea;
    --strip-text: #16137c;
  }
  * { margin: 0; padding: 0; box-sizing: border-box; }
  html, body { width: 1200px; height: 900px; overflow: hidden; }
  body {
    background: var(--backdrop);
    position: relative;
    font-family: "Source Sans 3", Arial, sans-serif;
  }
  .card {
    position: absolute;
    width: 600px;
    height: 343px;
    border-radius: 2px;
    box-shadow: 0 10px 28px rgba(0,0,0,0.18);
    overflow: hidden;
  }
  .card-front {
    left: 230px;
    top: 90px;
    background: var(--paper);
    display: flex;
    align-items: center;
    justify-content: center;
  }
  .card-back {
    left: 370px;
    top: 470px;
    background: var(--paper);
  }
  .brand {
    display: flex;
    flex-direction: column;
    align-items: center;
    gap: 14px;
    color: var(--navy);
  }
  .brand-square {
    width: 26px;
    height: 26px;
    background: currentColor;
  }
  .brand-name {
    font-family: "Montserrat", Arial, sans-serif;
    font-weight: 300;
    font-size: 25px;
    letter-spacing: 1px;
    white-space: nowrap;
  }
  .back-panel {
    height: 292px;
    background: linear-gradient(160deg, var(--navy) 0%, var(--navy-deep) 100%);
    color: var(--paper);
    display: flex;
    flex-direction: column;
    align-items: center;
    padding-top: 48px;
  }
  .back-panel .brand { color: var(--paper); gap: 12px; }
  .back-panel .brand-name { font-size: 24px; }
  .contact {
    margin-top: 26px;
    text-align: center;
    line-height: 1.3;
  }
  .contact-name {
    font-weight: 700;
    font-size: 17px;
    text-transform: uppercase;
    letter-spacing: 0.3px;
  }
  .contact-line { font-size: 13.5px; }
  .contact-label { font-weight: 700; }
  .web-strip {
    height: 51px;
    display: flex;
    align-items: center;
    justify-content: center;
    font-family: "Montserrat", Arial, sans-serif;
    font-weight: 700;
    font-size: 13px;
    letter-spacing: 3.5px;
    color: var(--strip-text);
    text-transform: uppercase;
  }
</style>
</head>
<body>
  <section class="card card-front">
    <div class="brand">
      <span class="brand-square"></span>
      <span class="brand-name">FERNCLIFF ADVISORY</span>
    </div>
  </section>

  <section class="card card-back">
    <div class="back-panel">
      <div class="brand">
        <span class="brand-square"></span>
        <span class="brand-name">FERNCLIFF ADVISORY</span>
      </div>
      <div class="contact">
        <p class="contact-name">Daniel Whitcombe</p>
        <p class="contact-line">2870 North 9th Avenue, Summit Floor, Elm Ridge, Illinois 60531</p>
        <p class="contact-line"><span class="contact-label">Email:</span> dan@ferncliffadvisory.com</p>
      </div>
    </div>
    <div class="web-strip">www.ferncliffadvisory.com</div>
  </section>
</body>
</html>
```